Business card design Needed for new logo / Construction business, home extensions and new builds

We need a business card design using our new logo files which i will attach to this project :)

We are a small construction business specialising in home extensions, new builds and property development. We are very ambitious and would appreciate professional and elegant designs for our new business card.

Very serious about using the services on MakerQuarry and recently acquired our new logo from here :)

Please get involved, i will feedback when i can as i am very busy but can respond daily, thanks

Target Market(s)

People that want to build onto their houses, new building developments or adding too their existing property

Industry/Entity Type

Construction

Contact Information for Business Card

Renwick Tolliver Construction, Lionel Ashby (Managing Director), Tel 07822254961, email - info@renwick-tolliver, www.renwick-tolliver.co.uk

Colors

Designer to choose colors to be used in the design.

Requirements
Must have
• I like a deep grey on the back please. A lot of you have provided black from and back, try mixing things up a little. The black looks cool 😎 Thanks

```html
<!DOCTYPE html>
<html lang="en">
<head>
<meta charset="utf-8">
<title>Renwick Tolliver Construction – Business Card</title>
<link rel="stylesheet" href="https://fonts.googleapis.com/css2?family=Cinzel:wght@500;600&family=Lato:wght@400;700&display=swap">
<style>
  :root {
    --backdrop: #242424;
    --card-front: #1a1a1a;
    --card-back: #343434;
    --gold: #e0a92c;
    --silver: #d9d9d9;
    --text: #ececec;
  }
  * { box-sizing: border-box; margin: 0; padding: 0; }
  html, body { width: 1200px; height: 875px; overflow: hidden; }
  body {
    background: var(--backdrop);
    position: relative;
    font-family: "Lato", sans-serif;
  }
  .card {
    position: absolute;
    width: 540px;
    height: 310px;
    border-radius: 16px;
  }
  .card--front { left: 60px; top: 100px; background: var(--card-front); }
  .card--back  { left: 600px; top: 470px; background: var(--card-back); }

  /* Front */
  .front-brand {
    position: absolute; inset: 0;
    display: flex; flex-direction: column; align-items: center; justify-content: center;
    gap: 12px;
  }
  .front-brand__mark { width: 26px; height: 26px; background: var(--gold); margin-bottom: 8px; }
  .front-brand__name {
    font-family: "Cinzel", serif; font-weight: 600; color: var(--gold);
    font-size: 30px; letter-spacing: 2px; text-transform: uppercase; text-align: center;
    line-height: 1.2;
  }
  .front-brand__rule { display: flex; align-items: center; gap: 220px; width: 360px; margin-top: -2px; }
  .front-brand__rule span { flex: 1; height: 2px; background: var(--gold); }

  /* Back */
  .holder { position: absolute; left: 34px; top: 92px; width: 290px; }
  .holder__name {
    font-family: "Cinzel", serif; font-weight: 600; color: var(--silver);
    font-size: 22px; letter-spacing: 1.5px; text-transform: uppercase; white-space: nowrap;
  }
  .holder__role { color: var(--gold); font-weight: 700; font-size: 14px; margin-top: 2px; }
  .holder__rule { width: 70px; height: 1px; background: var(--silver); margin: 9px 0 11px; }
  .contact { list-style: none; }
  .contact li {
    display: flex; align-items: flex-start; gap: 10px;
    color: var(--text); font-size: 12.5px; line-height: 1.35; margin-bottom: 4px;
  }
  .contact svg { flex: none; width: 13px; height: 13px; fill: var(--gold); margin-top: 2px; }
  .back-brand {
    position: absolute; right: 26px; top: 28px; width: 220px; height: 180px;
    display: flex; flex-direction: column; align-items: center; justify-content: center; gap: 14px;
  }
  .back-brand__mark { width: 30px; height: 30px; background: var(--gold); }
  .back-brand__name {
    font-family: "Cinzel", serif; font-weight: 600; color: var(--gold);
    font-size: 24px; letter-spacing: 1px; text-transform: uppercase; text-align: center; line-height: 1.2;
  }
</style>
</head>
<body>

<section class="card card--front" aria-label="Card front">
  <div class="front-brand">
    <div class="front-brand__mark"></div>
    <p class="front-brand__name">Renwick Tolliver<br>Construction</p>
    <div class="front-brand__rule"><span></span><span></span></div>
  </div>
</section>

<section class="card card--back" aria-label="Card back">
  <div class="back-brand">
    <div class="back-brand__mark"></div>
    <p class="back-brand__name">Renwick<br>Tolliver</p>
  </div>
  <div class="holder">
    <h1 class="holder__name">Dorian Whitlock</h1>
    <p class="holder__role">Founder &amp; CEO</p>
    <div class="holder__rule"></div>
    <ul class="contact">
      <li>
        <svg viewBox="0 0 16 16"><path d="M8 0a5.5 5.5 0 0 0-5.5 5.5C2.5 10 8 16 8 16s5.5-6 5.5-10.5A5.5 5.5 0 0 0 8 0zm0 8a2.5 2.5 0 1 1 0-5 2.5 2.5 0 0 1 0 5z"/></svg>
        <span>Your Address, City<br>State, Zip 1235</span>
      </li>
      <li>
        <svg viewBox="0 0 16 16"><path d="M3.6 1l2.3 2.6-1.3 2a9 9 0 0 0 5.8 5.8l2-1.3L15 12.4 13.3 15C6.8 14.4 1.6 9.2 1 2.7z"/></svg>
        <span>(123) 456-7890</span>
      </li>
      <li>
        <svg viewBox="0 0 16 16"><path d="M4 0h8a1 1 0 0 1 1 1v14a1 1 0 0 1-1 1H4a1 1 0 0 1-1-1V1a1 1 0 0 1 1-1zm1 2v10h6V2zm3 11a1 1 0 1 0 0 2 1 1 0 0 0 0-2z"/></svg>
        <span>(231) 456-7890</span>
      </li>
      <li>
        <svg viewBox="0 0 16 16"><path d="M4 1h8v4H4zM1 6h14v6h-3v3H4v-3H1zm4 4v3h6v-3z"/></svg>
        <span>(312) 456-7890</span>
      </li>
      <li>
        <svg viewBox="0 0 16 16"><path d="M0 3h16v1L8 9 0 4zm0 3l8 5 8-5v7H0z"/></svg>
        <span>office@yourwebsite.com</span>
      </li>
      <li>
        <svg viewBox="0 0 16 16"><path d="M8 0a8 8 0 1 0 0 16A8 8 0 0 0 8 0zm0 1.5c.9 0 2 1.9 2.3 5.2H5.7C6 3.4 7.1 1.5 8 1.5zM1.6 8.8h2.6c.1 2 .5 3.7 1.1 4.9a6.6 6.6 0 0 1-3.7-4.9zm0-2.1a6.6 6.6 0 0 1 3.7-4.4c-.6 1.1-1 2.6-1.1 4.4zm6.4 7.8c-.9 0-2-1.9-2.3-5.7h4.6c-.3 3.8-1.4 5.7-2.3 5.7zm2.7-.8c.6-1.2 1-2.9 1.1-4.9h2.6a6.6 6.6 0 0 1-3.7 4.9zm1.1-7c-.1-1.8-.5-3.3-1.1-4.4a6.6 6.6 0 0 1 3.7 4.4z"/></svg>
        <span>www.yourwebsite.com</span>
      </li>
    </ul>
  </div>
</section>

</body>
</html>
```